BOLD & MINIMALIST DESIGN NEEDED

We want a very bold but minimalistic business card design that is impactful and utilizes both sides of the business card. Our current logo is included for your use.

We want bold fonts and good use of negative space. We don't want the logo to overpower the design.

Target Market(s)

Professionals who are building new commercial buildings.

Industry/Entity Type

Construction

Contact Information for Business Card

Name, Title, email, office phone, cell phone, website

Font styles to use
Serif
Sans Serif

Requirements
Must have
• Bold design!

```html
<!DOCTYPE html>
<html lang="en">
<head>
<meta charset="utf-8">
<title>Ridgecrest Design + Build — Business Card</title>
<link rel="stylesheet" href="https://fonts.googleapis.com/css2?family=Montserrat:wght@400;500;700&display=swap">
<style>
  :root {
    --stage: #979797;
    --card-dark: #141414;
    --brand-green: #86c440;
    --green-light: #d6ebbd;
    --green-mid: #86c440;
    --green-deep: #3d7a34;
    --white: #ffffff;
  }
  * { box-sizing: border-box; margin: 0; padding: 0; }
  html, body {
    width: 1200px; height: 1108px; overflow: hidden;
    background: var(--stage);
    font-family: "Montserrat", sans-serif;
  }
  .canvas { position: relative; width: 1200px; height: 1108px; }
  .card {
    position: absolute; left: 240px; width: 718px; height: 411px;
    border-radius: 30px; overflow: hidden;
  }
  .card-front { top: 119px; }
  .front-pattern {
    position: absolute; inset: 0;
    background: linear-gradient(115deg, var(--green-light) 0%, #b9dc92 30%, var(--green-mid) 52%, #5c9e3f 72%, var(--green-deep) 100%);
  }
  .card-back { top: 581px; background: var(--card-dark); color: var(--white); }
  .brand {
    position: absolute; top: 128px; left: 0; right: 0;
    display: flex; justify-content: center; align-items: center; gap: 12px;
  }
  .brand-square { width: 22px; height: 22px; background: var(--brand-green); }
  .brand-name { font-weight: 700; font-size: 28px; letter-spacing: 1px; color: var(--white); }
  .person { position: absolute; right: 389px; top: 240px; text-align: right; }
  .person-name { font-weight: 700; font-size: 33px; color: var(--brand-green); letter-spacing: 0.5px; line-height: 1; }
  .person-title { margin-top: 12px; font-weight: 400; font-size: 17px; letter-spacing: 0.5px; }
  .divider { position: absolute; left: 356px; top: 223px; width: 2px; height: 102px; background: var(--brand-green); }
  .contact-list { position: absolute; left: 387px; top: 220px; list-style: none; }
  .contact-item { display: flex; align-items: center; height: 29px; font-size: 18px; letter-spacing: 0.4px; }
  .contact-icon { width: 16px; height: 16px; margin-right: 10px; fill: var(--brand-green); }
  .address-band {
    position: absolute; left: 0; right: 0; top: 359px; height: 25px;
    background: var(--brand-green); text-align: center;
    font-size: 17px; line-height: 25px; letter-spacing: 0.4px; color: var(--white);
  }
</style>
</head>
<body>
<main class="canvas">
  <section class="card card-front">
    <div class="front-pattern" role="img" aria-label="Repeating pattern of the company mark in shades of green"></div>
  </section>

  <section class="card card-back">
    <div class="brand">
      <span class="brand-square"></span>
      <span class="brand-name">RIDGECREST DESIGN + BUILD</span>
    </div>

    <div class="person">
      <p class="person-name">MARCUS HALE</p>
      <p class="person-title">OWNER-CEO</p>
    </div>

    <div class="divider"></div>

    <ul class="contact-list">
      <li class="contact-item">
        <svg class="contact-icon" viewBox="0 0 16 16"><path d="M1 6c0-2 3-3 7-3s7 1 7 3v1h-4V5.5C10 5 6 5 5 5.5V7H1z"/><path d="M3 8h10l1 6H2z"/></svg>
        123 456 789
      </li>
      <li class="contact-item">
        <svg class="contact-icon" viewBox="0 0 16 16"><path d="M4 1h8v14H4z M5.5 2.5v9h5v-9z M7 12.5h2v1H7z" fill-rule="evenodd"/></svg>
        123 456 789
      </li>
      <li class="contact-item">
        <svg class="contact-icon" viewBox="0 0 16 16"><path d="M1 4h14v1L8 9.5 1 5z"/><path d="M1 6.5l7 4.5 7-4.5V12H1z"/></svg>
        info@yourmail.com
      </li>
      <li class="contact-item">
        <svg class="contact-icon" viewBox="0 0 16 16"><circle cx="8" cy="8" r="7"/><path d="M4 4c2 1 1 3 3 3s1 3 2 4M10 3c1 2 3 2 4 4" stroke="#141414" stroke-width="1.3" fill="none"/></svg>
        www.yourwebsite.com
      </li>
    </ul>

    <div class="address-band">Your address, City State, Zip 1234</div>
  </section>
</main>
</body>
</html>
```